business card

Business card for new business.
Red and black corporate colors.
Card can have an Indsutrial feel to it. Feel free to add Rust, Bolted steel, or graphics as you see fit. We provide highly specialized services to the below mentioned industries.
Keep information out of corners so that if I want I can choose rounded corners.
Information
- front. name - title - phone - email
- Rear
Refining - Rail - Infrastructure - Mining - Energy
Calgary - Edmonton - Fort McMurray - Revelstoke - Vancouver

```html
<!DOCTYPE html>
<html lang="en">
<head>
<meta charset="utf-8">
<title>Girderline Business Card</title>
<link rel="stylesheet" href="https://fonts.googleapis.com/css2?family=Roboto:wght@400;500&family=Roboto+Condensed:wght@700&display=swap">
<style>
  :root {
    --backdrop: #1e1e1e;
    --brand-red: #e30613;
    --steel-light: #f2f2f2;
    --steel-mid: #d9d9d9;
    --steel-dark: #c4c4c4;
    --text-grey: #5a5a5a;
    --logo-grey: #7d7d7d;
    --white: #ffffff;
  }
  * { margin: 0; padding: 0; box-sizing: border-box; }
  html, body {
    width: 1200px;
    height: 960px;
    overflow: hidden;
    background: var(--backdrop);
  }
  .canvas { position: relative; width: 1200px; height: 960px; }

  .card {
    position: absolute;
    width: 600px;
    height: 343px;
    box-shadow: 0 2px 6px rgba(0,0,0,0.5);
  }

  /* Front */
  .card-front {
    left: 314px;
    top: 113px;
    background:
      repeating-linear-gradient(90deg, rgba(255,255,255,0.25) 0 1px, rgba(0,0,0,0.03) 1px 3px, rgba(255,255,255,0.1) 3px 5px),
      linear-gradient(180deg, var(--steel-dark) 0%, var(--steel-light) 35%, var(--steel-mid) 70%, var(--steel-dark) 100%);
  }
  .brand {
    position: absolute;
    left: 30px;
    top: 38px;
    display: flex;
    align-items: center;
    gap: 10px;
  }
  .brand-square {
    width: 30px;
    height: 30px;
    background: var(--brand-red);
  }
  .brand-name {
    font-family: "Roboto Condensed", "Arial Narrow", sans-serif;
    font-weight: 700;
    font-size: 44px;
    line-height: 1;
    color: var(--logo-grey);
    letter-spacing: 0.5px;
  }
  .contact-list {
    position: absolute;
    left: 30px;
    top: 253px;
    list-style: none;
    font-family: "Roboto", Arial, sans-serif;
    font-size: 15px;
    line-height: 19px;
    color: var(--text-grey);
  }
  .contact-list li { display: flex; align-items: center; gap: 8px; }
  .contact-icon { width: 12px; height: 12px; fill: var(--brand-red); flex: none; }
  .person {
    position: absolute;
    right: 30px;
    top: 266px;
    text-align: right;
  }
  .person-name {
    font-family: "Roboto Condensed", "Arial Narrow", sans-serif;
    font-weight: 700;
    font-size: 24px;
    line-height: 26px;
    color: var(--brand-red);
  }
  .person-title {
    font-family: "Roboto", Arial, sans-serif;
    font-weight: 500;
    font-size: 15px;
    line-height: 18px;
    color: var(--logo-grey);
  }
  .name-pointer {
    position: absolute;
    right: 0;
    top: 275px;
    width: 0;
    height: 0;
    border-top: 13px solid transparent;
    border-bottom: 13px solid transparent;
    border-right: 19px solid var(--brand-red);
  }

  /* Back */
  .card-back {
    left: 311px;
    top: 472px;
    width: 601px;
    background: var(--brand-red);
    color: var(--white);
    text-align: center;
  }
  .back-brand {
    position: absolute;
    left: 0;
    right: 0;
    top: 100px;
    display: flex;
    justify-content: center;
    align-items: center;
    gap: 14px;
  }
  .back-brand .brand-square { background: var(--white); width: 40px; height: 40px; }
  .back-brand .brand-name { color: var(--white); font-size: 58px; }
  .services {
    position: absolute;
    left: 0;
    right: 0;
    top: 257px;
    font-family: "Roboto", Arial, sans-serif;
    font-size: 15px;
    line-height: 18px;
  }
</style>
</head>
<body>
<main class="canvas">
  <section class="card card-front">
    <div class="brand">
      <span class="brand-square"></span>
      <span class="brand-name">GIRDERLINE</span>
    </div>
    <ul class="contact-list">
      <li>
        <svg class="contact-icon" viewBox="0 0 24 24"><path d="M6.6 10.8a15 15 0 0 0 6.6 6.6l2.2-2.2a1 1 0 0 1 1-.25 11.4 11.4 0 0 0 3.6.57 1 1 0 0 1 1 1V20a1 1 0 0 1-1 1A17 17 0 0 1 3 4a1 1 0 0 1 1-1h3.5a1 1 0 0 1 1 1c0 1.25.2 2.45.57 3.57a1 1 0 0 1-.25 1z"/></svg>
        604 555 0182
      </li>
      <li>
        <svg class="contact-icon" viewBox="0 0 24 24"><path d="M2 5h20v14H2z"/><path d="M3 6l9 7 9-7" fill="none" stroke="#fff" stroke-width="1.5"/></svg>
        info@girderline.com
      </li>
      <li>
        <svg class="contact-icon" viewBox="0 0 24 24"><circle cx="12" cy="12" r="10"/><path d="M2 12h20M12 2c3 3 3 17 0 20M12 2c-3 3-3 17 0 20" fill="none" stroke="#fff" stroke-width="1.5"/></svg>
        www.girderline.com
      </li>
    </ul>
    <div class="person">
      <p class="person-name">MARK DALTON</p>
      <p class="person-title">CEO/FOUNDER</p>
    </div>
    <span class="name-pointer"></span>
  </section>

  <section class="card card-back">
    <div class="back-brand">
      <span class="brand-square"></span>
      <span class="brand-name">GIRDERLINE</span>
    </div>
    <p class="services">
      Pipelines • Rigging • Fabrication • Steel<br>
      Utilities • Ashford • Kellan Bay • Port Rowley<br>
      Millbrook • Stonehaven
    </p>
  </section>
</main>
</body>
</html>
```